BildeVOLD buisnesscard

Hey :) I need a modern buisnesscard for my company BildeVOLD
It most have:
Dagligleder og Fotograf: Henrik Audun Strandvik

Mob: +4791264085
Epost: post@bildevold.example
Adresse: Kvernbakken9, 6040 Langevåg

Facbook and instagram logo with text BildeVOLD

BildeVOLD logo

It Company

```html
<!DOCTYPE html>
<html lang="no">
<head>
<meta charset="utf-8">
<title>BildeVOLD – visittkort</title>
<link rel="stylesheet" href="https://fonts.googleapis.com/css2?family=Noto+Sans:wght@400;700&display=swap">
<style>
  :root {
    --blue: #3399c8;
    --blue-deep: #2f8cbc;
    --pink: #d3589b;
    --pink-deep: #cc4d8e;
    --panel: #262626;
    --ink: #1e2a36;
    --ink-pink: #2a1a24;
    --backdrop: #ebe8e4;
  }
  * { box-sizing: border-box; margin: 0; padding: 0; }
  html, body { width: 1200px; height: 1200px; overflow: hidden; }
  body {
    background: var(--backdrop);
    font-family: "Noto Sans", sans-serif;
    position: relative;
  }
  .card {
    position: absolute;
    left: 239px;
    width: 722px;
    height: 435px;
  }
  .card--front { top: 106px; background: linear-gradient(135deg, var(--blue), var(--blue-deep)); }
  .card--back { top: 624px; background: linear-gradient(135deg, var(--pink), var(--pink-deep)); }
  .card__panel {
    position: absolute;
    left: 23px; top: 24px;
    width: 678px; height: 341px;
    background: var(--panel);
  }
  .bracket {
    position: absolute;
    width: 40px; height: 40px;
    border: 0 solid var(--accent);
  }
  .card--front .bracket { --accent: var(--blue); }
  .card--back .bracket { --accent: var(--pink); }
  .bracket--tl { left: 15px; top: 15px; border-left-width: 1.5px; border-top-width: 1.5px; }
  .bracket--tr { right: 15px; top: 15px; border-right-width: 1.5px; border-top-width: 1.5px; }
  .bracket--bl { left: 15px; bottom: 18px; border-left-width: 1.5px; border-bottom-width: 1.5px; }
  .bracket--br { right: 15px; bottom: 18px; border-right-width: 1.5px; border-bottom-width: 1.5px; }

  .person {
    position: absolute;
    left: 0; right: 0; top: 128px;
    text-align: center;
  }
  .person__name { color: var(--blue); font-size: 27px; line-height: 1; letter-spacing: 0.3px; }
  .person__mark { display: block; margin: 12px auto 6px; }
  .person__role { color: var(--pink); font-size: 18px; line-height: 1; }

  .contact {
    position: absolute;
    left: 0; right: 0; top: 377px;
    text-align: center;
    color: var(--ink);
    font-size: 17.5px;
    line-height: 21px;
    letter-spacing: 0.2px;
  }

  .brand {
    position: absolute;
    left: 0; right: 0; top: 0; bottom: 0;
    display: flex;
    align-items: center;
    justify-content: center;
  }
  .brand__name {
    color: var(--blue);
    font-weight: 700;
    font-size: 52px;
    letter-spacing: 0.5px;
  }

  .social {
    position: absolute;
    left: 0; right: 0; top: 382px;
    display: flex;
    justify-content: center;
    gap: 22px;
    color: var(--ink-pink);
    font-size: 19px;
  }
  .social__item { display: flex; align-items: center; gap: 12px; }
  .social__dot {
    width: 33px; height: 33px;
    border: 2px solid var(--ink-pink);
    border-radius: 50%;
  }
</style>
</head>
<body>
  <section class="card card--front">
    <div class="card__panel">
      <span class="bracket bracket--tl"></span>
      <span class="bracket bracket--tr"></span>
      <span class="bracket bracket--bl"></span>
      <span class="bracket bracket--br"></span>
      <div class="person">
        <p class="person__name">Henrik Audun Strandvik</p>
        <svg class="person__mark" width="18" height="18" viewBox="0 0 18 18" aria-hidden="true">
          <circle cx="9" cy="9" r="8" fill="none" stroke="var(--blue)" stroke-width="1.3"/>
          <circle cx="9" cy="9" r="4.5" fill="none" stroke="var(--blue)" stroke-width="1.3"/>
        </svg>
        <p class="person__role">Dagligleder og Fotograf</p>
      </div>
    </div>
    <p class="contact">M: 912 640 85 | www.bildevold.example | post@bildevold.example<br>Kvernbakken9, 6040 Langevåg</p>
  </section>

  <section class="card card--back">
    <div class="card__panel">
      <span class="bracket bracket--tl"></span>
      <span class="bracket bracket--tr"></span>
      <span class="bracket bracket--bl"></span>
      <span class="bracket bracket--br"></span>
      <div class="brand">
        <span class="brand__name">BildeVOLD</span>
      </div>
    </div>
    <div class="social">
      <span class="social__item"><span class="social__dot"></span>BildeVOLD</span>
      <span class="social__item"><span class="social__dot"></span>BildeVOLD</span>
    </div>
  </section>
</body>
</html>
```